Now Leasing Banner

Looking for a banner that says the following information approx 4' x 30'

Now Leasing Maplebrook Terrace 925-318-6042

Target Market(s)

Drive by traffic

Industry/Entity Type

Residential property management

Requirements
Must have
• Clear and readable from a distance

```html
<!DOCTYPE html>
<html lang="en">
<head>
<meta charset="utf-8">
<title>Now Leasing Maplebrook Terrace</title>
<link rel="stylesheet" href="https://fonts.googleapis.com/css2?family=Jost:wght@300;400;700&display=swap">
<style>
  :root {
    --navy: #2b3179;
    --glow: #4aa3dc;
    --beam: #3a5a9e;
    --white: #ffffff;
  }
  html, body {
    margin: 0;
    padding: 0;
    width: 1200px;
    height: 160px;
    overflow: hidden;
    background: var(--navy);
  }
  .banner {
    display: block;
    width: 1200px;
    height: 160px;
  }
  .banner__kicker {
    font-family: "Jost", sans-serif;
    font-weight: 300;
    font-size: 36px;
    fill: var(--white);
  }
  .banner__headline {
    font-family: "Jost", sans-serif;
    font-weight: 700;
    font-size: 92px;
    fill: var(--white);
  }
  .banner__phone {
    font-family: "Jost", sans-serif;
    font-weight: 400;
    font-size: 21px;
    fill: var(--white);
  }
</style>
</head>
<body>
<svg class="banner" viewBox="0 0 1200 160" xmlns="http://www.w3.org/2000/svg">
  <defs>
    <radialGradient id="glow-left" cx="93" cy="84" r="170" gradientUnits="userSpaceOnUse">
      <stop offset="0" stop-color="var(--glow)" stop-opacity="0.95"/>
      <stop offset="1" stop-color="var(--glow)" stop-opacity="0"/>
    </radialGradient>
    <radialGradient id="glow-right" cx="1088" cy="70" r="160" gradientUnits="userSpaceOnUse">
      <stop offset="0" stop-color="var(--glow)" stop-opacity="0.9"/>
      <stop offset="1" stop-color="var(--glow)" stop-opacity="0"/>
    </radialGradient>
  </defs>

  <rect class="banner__field" width="1200" height="160" fill="var(--navy)"/>

  <g class="banner__beams">
    <polygon points="0,149 214,0 289,0 9,160 0,160" fill="var(--beam)" opacity="0.55"/>
    <polygon points="0,0 140,0 0,100" fill="url(#glow-left)" opacity="0.6"/>
    <rect x="0" y="0" width="300" height="160" fill="url(#glow-left)"/>
    <polygon points="908,0 969,0 1200,116 1200,154" fill="var(--beam)" opacity="0.55"/>
    <polygon points="1040,0 1200,0 1200,80" fill="var(--beam)" opacity="0.45"/>
    <rect x="900" y="0" width="300" height="160" fill="url(#glow-right)"/>
  </g>

  <text class="banner__kicker" x="60" y="40.5" textLength="86" lengthAdjust="spacingAndGlyphs">NOW</text>
  <text class="banner__headline" x="58" y="119" textLength="1083" lengthAdjust="spacingAndGlyphs">LEASING MAPLEBROOK TERRACE</text>
  <text class="banner__phone" x="948" y="145" textLength="180" lengthAdjust="spacing">925-318-6042</text>
</svg>
</body>
</html>
```